Colin Vardek Business card

Hey there, I’m hoping to have a business card designed. I’m in Real estate and just switched to a new Brokerage called: The Harbourline Property Group

The back could just be the company name maybe or whatever looks good!

I’ve attached some logos of our company and some cards my buddy had done up.

On the card:
Colin Vardek
colinvardek@mailora.com
587-412-9065
colinvardek.ca

Target Market(s)

Home buyers and sellers

Industry/Entity Type

Real Estate

Contact Information for Business Card

just looking for a cool and modern design with my picture on it. I like the idea of Black and red being used.

Requirements
Must have
• all the details provided. I'm open to anything. Just want a professional looking card.

```html
<!DOCTYPE html>
<html lang="en">
<head>
<meta charset="utf-8">
<title>Colin Vardek – Business Card</title>
<link href="https://fonts.googleapis.com/css2?family=Roboto:wght@400;500;700&display=swap" rel="stylesheet">
<style>
  :root {
    --backdrop: #2b2b2d;
    --card: #242227;
    --card-deep: #1a191d;
    --red: #d21f3c;
    --white: #f4f4f4;
    --photo-light: #e9e9ea;
    --photo-dark: #2c2f3a;
  }
  * { box-sizing: border-box; margin: 0; padding: 0; }
  html, body {
    width: 1200px; height: 852px; overflow: hidden;
    background: var(--backdrop);
    font-family: "Roboto", sans-serif;
  }
  .canvas { position: relative; width: 1200px; height: 852px; }
  .card {
    position: absolute; width: 540px; height: 310px;
    background: var(--card);
    border-radius: 22px;
    box-shadow: 0 3px 0 var(--red), 0 12px 30px rgba(0,0,0,.45);
    overflow: hidden;
  }
  .card--front { left: 330px; top: 70px; }
  .card--back { left: 330px; top: 470px; }

  .brand-name {
    position: absolute; inset: 0;
    display: flex; align-items: center; justify-content: center;
    text-align: center;
    font-weight: 700; font-size: 34px; line-height: 1.15;
    color: var(--white); letter-spacing: .5px;
    padding: 0 60px;
  }

  .back-accent {
    position: absolute; right: 0; top: 0; width: 230px; height: 100%;
    background: linear-gradient(160deg, #2c2b31 0%, var(--card-deep) 70%);
  }
  .portrait-ring {
    position: absolute; left: 60px; top: 30px;
    width: 150px; height: 150px; border-radius: 50%;
    border: 3px solid var(--red); padding: 6px;
    background: var(--card);
  }
  .portrait {
    width: 100%; height: 100%; border-radius: 50%;
    background: radial-gradient(circle at 50% 40%, var(--photo-light) 45%, var(--photo-dark) 100%);
  }
  .side-bar {
    position: absolute; left: 0; top: 218px; width: 28px; height: 40px;
    background: var(--red);
  }
  .agent-name {
    position: absolute; left: 60px; top: 198px;
    color: var(--red); font-weight: 700; font-size: 24px;
  }
  .contact-list {
    position: absolute; left: 60px; top: 232px; list-style: none;
    color: var(--white); font-size: 15px; line-height: 22px;
  }
  .contact-list li { display: flex; align-items: center; gap: 8px; }
  .contact-list svg { width: 13px; height: 13px; fill: var(--red); flex: none; }
</style>
</head>
<body>
<main class="canvas">
  <section class="card card--front">
    <p class="brand-name">The Harbourline Property Group</p>
  </section>

  <section class="card card--back">
    <div class="back-accent"></div>
    <div class="portrait-ring">
      <div class="portrait" role="img" aria-label="Portrait photo of Colin Vardek"></div>
    </div>
    <div class="side-bar"></div>
    <h1 class="agent-name">Colin Vardek</h1>
    <ul class="contact-list">
      <li>
        <svg viewBox="0 0 24 24" aria-hidden="true"><path d="M6.6 10.8a15 15 0 0 0 6.6 6.6l2.2-2.2a1 1 0 0 1 1-.25 11.4 11.4 0 0 0 3.6.57 1 1 0 0 1 1 1V20a1 1 0 0 1-1 1A17 17 0 0 1 3 4a1 1 0 0 1 1-1h3.5a1 1 0 0 1 1 1c0 1.25.2 2.45.57 3.57a1 1 0 0 1-.25 1z"/></svg>
        587-412-9065
      </li>
      <li>
        <svg viewBox="0 0 24 24" aria-hidden="true"><path d="M3 5h18a1 1 0 0 1 1 1v12a1 1 0 0 1-1 1H3a1 1 0 0 1-1-1V6a1 1 0 0 1 1-1zm9 7.5L20 7H4z"/></svg>
        colinvardek@mailora.com
      </li>
      <li>
        <svg viewBox="0 0 24 24" aria-hidden="true"><circle cx="12" cy="12" r="10"/></svg>
        colinvardek.ca
      </li>
    </ul>
  </section>
</main>
</body>
</html>
```